Protective Security Officer services company needs logo and e mail stationary design

We need a logo design that compliments our vehicle wraps. We provide armed guards to the federal government. We want to use patriotic flag colors of red, white and blue. We like the name ORVA with the red swish. See vehicle pictures.
We provide armed guards to various departments of the federal government including : Civic Shield Bureau, National Guardpost Agency, All of the armed forces Navy , Air Force, Army, Coast Guard.

Target Market(s)

Federal government, all the armed forces , large government contractors in the security industry

Contact Information for Business Card

we want a QR code linking to our website

Logo Text

I want our name ORVA in the logo with the red white and blue color scheme srr pictures of our vehicles

Colors
ec1f27
ffffff
0255a3

Requirements
Must have
• name, position title, 2 or 3 phone numbers, e mail address
Nice to have
• some foil
Should not have
• n/a

```html
<!DOCTYPE html>
<html lang="en">
<head>
<meta charset="utf-8">
<title>ORVA Protective Services – Stationery</title>
<link href="https://fonts.googleapis.com/css2?family=Exo+2:wght@700&family=Open+Sans:wght@400;600&family=Arimo:wght@400&display=swap" rel="stylesheet">
<style>
:root{
  --red:#ec1f27;
  --blue:#0255a3;
  --white:#ffffff;
  --ink:#3a3a3a;
  --black:#111111;
  --bg:#e6e7e9;
  --label:#8a8c90;
}
*{margin:0;padding:0;box-sizing:border-box}
html,body{width:1200px;height:1200px;overflow:hidden;background:var(--bg)}
.canvas{position:relative;width:1200px;height:1200px}
.sheet{position:absolute;background:var(--white);overflow:hidden;box-shadow:0 2px 6px rgba(0,0,0,.12)}
.band{position:absolute;left:0;top:0;width:100%;display:block}
.band-bottom{top:auto;bottom:0}
.brand{position:absolute;font-family:"Exo 2",sans-serif;font-weight:700;color:var(--blue);text-align:center;line-height:1}
.brand-name{display:block;letter-spacing:.06em}
.brand-tag{display:block;letter-spacing:.08em;text-transform:uppercase}
.contact{font-family:Arimo,sans-serif;color:var(--black);list-style:none}
.contact li{display:flex;align-items:center}
.contact svg{flex:none;fill:var(--blue)}
.contact .web{color:var(--blue)}
.address{font-family:Arimo,sans-serif;color:var(--black);font-style:normal}

/* letterhead */
.letterhead{left:120px;top:160px;width:557px;height:713px}
.letterhead .brand{left:55px;top:38px;width:136px}
.letterhead .brand-name{font-size:30px}
.letterhead .brand-tag{font-size:7.4px;margin-top:4px}
.sender{position:absolute;left:388px;top:44px;font-family:Arimo,sans-serif}
.sender-name{font-family:"Exo 2",sans-serif;font-weight:700;font-size:9px;color:var(--blue);letter-spacing:.02em}
.sender-title{font-size:6.6px;color:var(--black)}
.letter{position:absolute;left:53px;top:128px;width:451px;font-family:"Open Sans",sans-serif;font-size:8.6px;color:var(--ink);line-height:11px}
.letter .date{margin-bottom:10px}
.letter .recipient{margin-bottom:30px}
.letter .salute{margin-bottom:20px}
.letter .body p{line-height:16px;text-align:justify;margin-bottom:16px}
.letter .closing{margin-top:28px}
.signature{width:130px;height:18px;margin:10px 0 4px;background:linear-gradient(90deg,rgba(58,58,58,.25),rgba(58,58,58,.08))}
.signer{font-size:10.5px;font-weight:600;color:var(--ink)}
.signer-role{margin-top:4px}
.letterhead .contact{position:absolute;left:42px;top:659px;font-size:8.3px;line-height:11px}
.letterhead .contact svg{width:7px;height:7px;margin-right:4px}
.letterhead .address{position:absolute;right:44px;top:652px;font-size:8.3px;line-height:11px;text-align:right}

/* envelope front */
.envelope-front{left:716px;top:373px;width:434px;height:217px}
.envelope-front .brand{left:37px;top:27px;width:94px}
.envelope-front .brand-name{font-size:20px}
.envelope-front .brand-tag{font-size:5.2px;margin-top:3px}
.envelope-front .address{position:absolute;left:37px;top:172px;font-size:7.8px;line-height:10.5px}

/* envelope back */
.envelope-back{left:716px;top:623px;width:430px;height:213px}
.envelope-back .brand{left:165px;top:12px;width:100px;color:var(--white)}
.envelope-back .brand-name{font-size:20px}
.envelope-back .brand-tag{font-size:5px;margin-top:3px}

/* email signature */
.sig-label{position:absolute;right:942px;top:985px;font-family:Arimo,sans-serif;font-size:18px;line-height:22px;color:var(--label);text-align:right}
.email-signature{left:286px;top:928px;width:657px;height:163px;box-shadow:none}
.email-signature .brand{left:40px;top:38px;width:153px}
.email-signature .brand-name{font-size:36px}
.email-signature .brand-tag{font-size:9.4px;margin-top:5px}
.email-signature .address{position:absolute;right:464px;top:96px;font-size:14px;line-height:16.5px;text-align:right}
.divider{position:absolute;left:215px;top:36px;width:1px;height:107px;background:#9a9a9a}
.email-signature .sender{left:238px;top:44px}
.email-signature .sender-name{font-size:17.5px}
.email-signature .sender-title{font-size:13.5px;margin-top:2px;color:#333}
.email-signature .contact{position:absolute;left:238px;top:92px;font-size:14px;line-height:16.5px}
.email-signature .contact svg{width:11px;height:11px;margin-right:6px}
</style>
</head>
<body>
<main class="canvas">

  <svg width="0" height="0" style="position:absolute" aria-hidden="true">
    <defs>
      <symbol id="icon-phone" viewBox="0 0 16 16"><path d="M2 6c0-2 2.5-3.5 6-3.5S14 4 14 6l-3 .5-.5-1.5h-5L5 6.5zM3.5 8.5 5 6.5h6l1.5 2V13h-9z"/></symbol>
      <symbol id="icon-mail" viewBox="0 0 16 16"><path d="M1 3h14v10H1zm1.5 1.5 5.5 4 5.5-4M2.5 11.5 6 8m7.5 3.5L10 8" stroke="#fff" stroke-width="1.2"/></symbol>
      <symbol id="icon-globe" viewBox="0 0 16 16"><circle cx="8" cy="8" r="7"/><path d="M5 4c1 1 3 1 3 3s-2 1-2 3 1 2 1 3M10 3c0 2 2 2 3 3" stroke="#fff" stroke-width="1.3" fill="none"/></symbol>
    </defs>
  </svg>

  <!-- Letterhead -->
  <article class="sheet letterhead">
    <svg class="band" width="557" height="34" viewBox="0 0 557 34" aria-hidden="true">
      <rect width="557" height="14" fill="var(--red)"/>
      <polygon points="0,16 557,16 557,19 0,33" fill="var(--blue)"/>
    </svg>
    <div class="brand"><span class="brand-name">ORVA</span><span class="brand-tag">Protective Services</span></div>
    <div class="sender">
      <div class="sender-name">MARISOL T HARGROVE, CPA</div>
      <div class="sender-title">Chief Financial Officer</div>
    </div>
    <div class="letter">
      <p class="date">Issuing Date: May 5, 2018</p>
      <p class="recipient">Name Of Employee Mr. XYZABC<br>Address of Employee<br>Address Line 2 etc..</p>
      <p class="salute">Dear Mr.XYZABC</p>
      <div class="body">
        <p>Lorem Ipsum has been the industry's standard dummy text ever since the 1500s, when an unknown printer took a galley of type and scrambled it to make a type specimen book. It has survived not only five centuries, but also the leap into electronic typesetting, remaining essentially unchanged. It was popularised in the 1960s with the release of Letterform sheets containing Lorem Ipsum passages, and more recently with desktop publishing software like Pagecraft Studio including versions of Lorem Ipsum.</p>
        <p>Lorem Ipsum is simply dummy text of the printing and typesetting industry. Lorem Ipsum has been the industry's standard dummy text ever since the 1500s, when an unknown printer took a galley of type and scrambled it to make a type specimen book.</p>
        <p>It has survived not only five centuries, but also the leap into electronic typesetting, remaining essentially unchanged. It was popularised in the 1960s with the release of Letterform sheets containing Lorem Ipsum passages.</p>
      </div>
      <p class="closing">Yours Sincerely</p>
      <div class="signature" role="img" aria-label="Handwritten signature of Declan Whitmore"></div>
      <p class="signer">Declan Whitmore</p>
      <p class="signer-role">Managing Director</p>
    </div>
    <ul class="contact">
      <li><svg><use href="#icon-phone"/></svg>(555) 014-2200 | (555) 014-7731</li>
      <li><svg><use href="#icon-mail"/></svg>info@orvaprotective.com</li>
      <li><svg><use href="#icon-globe"/></svg>www.<span class="web">orvaprotective</span>.com</li>
    </ul>
    <address class="address">4120 Ridgeline Rd NE<br>Suite A<br>Millbrook, NM 87000</address>
    <svg class="band band-bottom" width="557" height="11" viewBox="0 0 557 11" aria-hidden="true">
      <polygon points="0,0 276,0 273,11 0,11" fill="var(--red)"/>
      <polygon points="279,0 557,0 557,11 276,11" fill="var(--blue)"/>
    </svg>
  </article>

  <!-- Envelope front -->
  <article class="sheet envelope-front">
    <svg class="band" width="434" height="25" viewBox="0 0 434 25" aria-hidden="true">
      <rect width="434" height="9" fill="var(--red)"/>
      <polygon points="0,11 434,11 434,13 0,24" fill="var(--blue)"/>
    </svg>
    <div class="brand"><span class="brand-name">ORVA</span><span class="brand-tag">Protective Services</span></div>
    <address class="address">4120 Ridgeline Rd NE<br>Suite A<br>Millbrook, NM 87000</address>
    <svg class="band band-bottom" width="434" height="7" viewBox="0 0 434 7" aria-hidden="true">
      <polygon points="0,0 224,0 222,7 0,7" fill="var(--red)"/>
      <polygon points="227,0 434,0 434,7 225,7" fill="var(--blue)"/>
    </svg>
  </article>

  <!-- Envelope back -->
  <article class="sheet envelope-back">
    <svg class="band" width="430" height="51" viewBox="0 0 430 51" aria-hidden="true">
      <polygon points="0,0 430,0 413,51 17,51" fill="var(--blue)"/>
    </svg>
    <div class="brand"><span class="brand-name">ORVA</span><span class="brand-tag">Protective Services</span></div>
  </article>

  <!-- Email signature -->
  <p class="sig-label">Email<br>Signature</p>
  <article class="sheet email-signature">
    <svg class="band" width="657" height="29" viewBox="0 0 657 29" aria-hidden="true">
      <rect width="657" height="12" fill="var(--red)"/>
      <polygon points="0,14 657,14 657,17 0,28" fill="var(--blue)"/>
    </svg>
    <div class="brand"><span class="brand-name">ORVA</span><span class="brand-tag">Protective Services</span></div>
    <address class="address">4120 Ridgeline Rd NE<br>Suite A<br>Millbrook, NM 87000</address>
    <div class="divider"></div>
    <div class="sender">
      <div class="sender-name">MARISOL T HARGROVE, CPA</div>
      <div class="sender-title">Chief Financial Officer</div>
    </div>
    <ul class="contact">
      <li><svg><use href="#icon-phone"/></svg>(555) 014-2200 | (555) 014-7731</li>
      <li><svg><use href="#icon-mail"/></svg>info@orvaprotective.com</li>
      <li><svg><use href="#icon-globe"/></svg>www.<span class="web">orvaprotective</span>.com</li>
    </ul>
    <svg class="band band-bottom" width="657" height="9" viewBox="0 0 657 9" aria-hidden="true">
      <polygon points="0,0 216,0 213,9 0,9" fill="var(--red)"/>
      <polygon points="219,0 657,0 657,9 216,9" fill="var(--blue)"/>
    </svg>
  </article>

</main>
</body>
</html>
```